Dynamic Business Card for Sports Supplements Company

Hi! I'm looking for an awesome business card to match my existing sports supplement company. I have uploaded my current company logo and screenshot of the front page of my website.

I would like to have something dynamic and interesting and utilize the colors in the website - the reds and purples

The business card should be double sided and focus on a unique eye-catching design on the back and include all the relevant company info.

Most importantly, it should say somewhere: "Sign up on our website for a coupon code."

Target Market(s)

Mostly for women gym goers but it shouldn't be too feminine. It should be in keeping with the website design. It should flow and clearly be connected to it

Industry/Entity Type

Business

Contact Information for Business Card

Lorraine K. Vestal
CEO
LVestal@Quorvanexco.com
www.quorvanexco.com
555.417.3820
P.O. Box 47315
Halden, Oregon 00000

Sign up on our website for a coupon code

Font styles to use
Serif
Sans Serif
Other font styles liked:
• Novecento font family and "Quorvanex" is in AR Destine font

Requirements
Must have
• One side should be a bold Quorvanex logo design. Even just the symbol itself may be o.k. (see attached file)

```html
<!DOCTYPE html>
<html lang="en">
<head>
<meta charset="utf-8">
<title>Quorvanex Business Card</title>
<link rel="stylesheet" href="https://fonts.googleapis.com/css2?family=Michroma&family=Open+Sans:wght@400;600;700&display=swap">
<style>
  :root {
    --bg: #2b2b2d;
    --card-light: #ffffff;
    --card-dark: #131316;
    --red: #e41d26;
    --ink: #1f1f21;
    --ink-soft: #2e2e30;
    --white: #ffffff;
    --muted: #c9c9cc;
  }
  * { margin: 0; padding: 0; box-sizing: border-box; }
  html, body {
    width: 1200px; height: 900px; overflow: hidden;
    background: var(--bg);
    font-family: "Open Sans", Arial, sans-serif;
  }
  .stage {
    position: relative; width: 1200px; height: 900px;
    display: flex; align-items: center; justify-content: center; gap: 40px;
  }
  .card {
    width: 540px; height: 310px; border-radius: 22px;
    position: relative; overflow: hidden;
    box-shadow: 0 14px 30px rgba(0,0,0,0.45);
  }
  /* Front */
  .card-front { background: var(--card-light); color: var(--ink); }
  .front-brand {
    position: absolute; left: 40px; top: 134px;
    display: flex; align-items: center; gap: 9px;
  }
  .brand-square { width: 18px; height: 18px; background: var(--red); flex: none; }
  .front-brand .brand-square { width: 15px; height: 15px; }
  .front-brand .brand-name {
    font-family: "Michroma", Arial, sans-serif;
    font-size: 16px; color: var(--ink); letter-spacing: 1px;
  }
  .contact {
    position: absolute; left: 268px; top: 62px;
  }
  .contact-name {
    font-family: "Michroma", Arial, sans-serif;
    color: var(--red); font-size: 15px; font-weight: 400; letter-spacing: 1.5px;
    text-transform: uppercase;
  }
  .contact-role {
    font-weight: 700; font-size: 13px; color: var(--ink);
    margin: 4px 0 14px 12px;
  }
  .contact-list { list-style: none; }
  .contact-list li {
    display: flex; align-items: center; gap: 8px;
    font-size: 13px; line-height: 21px; color: var(--ink-soft);
  }
  .contact-list svg { width: 11px; height: 11px; fill: var(--red); flex: none; }
  .contact-address {
    font-size: 13px; line-height: 19px; color: var(--ink-soft);
    margin-top: 12px; margin-left: 19px;
  }
  /* Back */
  .card-back {
    background: radial-gradient(ellipse at 50% 40%, #26262b 0%, var(--card-dark) 70%);
    color: var(--white); text-align: center;
  }
  .back-brand {
    position: absolute; left: 0; right: 0; top: 100px;
    display: flex; align-items: center; justify-content: center; gap: 12px;
  }
  .back-brand .brand-name {
    font-family: "Michroma", Arial, sans-serif;
    font-size: 26px; color: var(--white); letter-spacing: 1px;
  }
  .tagline {
    position: absolute; left: 0; right: 0; top: 146px;
    font-size: 8px; letter-spacing: 3px; color: var(--muted);
  }
  .promo {
    position: absolute; left: 0; right: 0; top: 222px;
    font-size: 12px; font-weight: 600; color: var(--white);
  }
  .promo .accent { color: var(--red); }
</style>
</head>
<body>
<main class="stage">
  <section class="card card-front">
    <div class="front-brand">
      <span class="brand-square"></span>
      <span class="brand-name">QUORVANEX</span>
    </div>
    <div class="contact">
      <h1 class="contact-name">Lorraine K. Vestal</h1>
      <p class="contact-role">CEO</p>
      <ul class="contact-list">
        <li>
          <svg viewBox="0 0 12 12" aria-hidden="true"><path d="M1 3c0-1 1-2 2-2h6c1 0 2 1 2 2v1H9V3H3v1H1zM2 5h8l1 6H1z"/></svg>
          555.417.3820
        </li>
        <li>
          <svg viewBox="0 0 12 12" aria-hidden="true"><path d="M0 2h12v8H0zM1 3l5 4 5-4v-.2H1z" fill-rule="evenodd"/></svg>
          LVestal@Quorvanexco.com
        </li>
        <li>
          <svg viewBox="0 0 12 12" aria-hidden="true"><circle cx="6" cy="6" r="6"/></svg>
          www.quorvanexco.com
        </li>
      </ul>
      <p class="contact-address">P.O. Box 47315<br>Halden, Oregon 00000</p>
    </div>
  </section>

  <section class="card card-back">
    <div class="back-brand">
      <span class="brand-square"></span>
      <span class="brand-name">QUORVANEX</span>
    </div>
    <p class="tagline">STRENGTH BUILT DAILY</p>
    <p class="promo"><span class="accent">Sign up</span> on our website for a coupon code</p>
  </section>
</main>
</body>
</html>
```